Skincare company needing leaflet/flyer for selling products

Hi guys. I am needing a leaflet/flyer design for my new skincare business - Miroa skincare. Our products are all made in Australia from natural ingredients. The leaflet should specify that all products have - organic ingredients, cruelty free, no nasty chemicals or ingredients and a made in Australia logo.
The pictures I have supplied, if they can be made more professional looking for the design without any background that would be great. It should look like other competitors and very appealing. The leaflet can be double sided so it looks more easy to read
The information is provided as follows:
Product, skin types the product is for, ml capacity of bottle, key ingredients and price.
Contact is a whatsapp number and website will be up later so if a leaflet can be made with and without the website.
This leaflet/flyer can be easy to read, not hard on the eyes and easy to understand. Focus on blue shades and other calm colours to make it easy on the eyes and attractive to see. Thank you guys for helping
Getting professional product photos done that can be updated on the leaflet/flyers once received. More submissions are welcomed
People wanting good quality skincare that does not contain harmful chemicals and is organic

```html
<!DOCTYPE html>
<html lang="en">
<head>
<meta charset="utf-8">
<title>Miroa skincare – Eye Cream flyer</title>
<link href="https://fonts.googleapis.com/css2?family=Audiowide&family=Open+Sans:wght@400;600&family=Arimo:wght@400;700&display=swap" rel="stylesheet">
<style>
  :root {
    --page-bg: #e9e8ec;
    --paper: #f7f6f9;
    --paper-shade: #ecebf0;
    --violet: #7a6fb0;
    --violet-dark: #6a5fa2;
    --ink-soft: #8a81bd;
    --white: #ffffff;
    --bottle-light: #fbfaf7;
    --bottle-warm: #f2dfc4;
  }
  * { box-sizing: border-box; margin: 0; padding: 0; }
  html, body { width: 1200px; height: 800px; overflow: hidden; }
  body {
    background: var(--page-bg);
    display: flex; align-items: center; justify-content: center;
    font-family: "Open Sans", sans-serif;
  }
  .flyer {
    position: relative;
    width: 588px; height: 760px;
    background: linear-gradient(160deg, var(--paper-shade) 0%, var(--paper) 45%, var(--white) 100%);
    box-shadow: 0 6px 24px rgba(60, 55, 90, 0.18);
    color: var(--violet);
    overflow: hidden;
  }
  .title {
    position: absolute; left: 70px; top: 50px; width: 460px;
    font-family: "Audiowide", sans-serif; font-weight: 400;
    color: var(--violet);
    line-height: 0.95; letter-spacing: 2px;
  }
  .title .word-eye { display: block; font-size: 84px; padding-left: 64px; }
  .title .word-cream { display: block; font-size: 84px; }
  .title-rule {
    position: absolute; left: 40px; top: 250px; width: 440px; height: 1px;
    background: var(--violet);
  }
  .product-photo {
    position: absolute; left: 56px; top: 276px; width: 180px; height: 256px;
    border-radius: 90px 90px 24px 24px;
    background: linear-gradient(100deg, var(--bottle-warm) 0%, var(--bottle-light) 40%, var(--bottle-light) 70%, var(--bottle-warm) 100%);
    box-shadow: 0 18px 22px -12px rgba(90, 85, 110, 0.35);
  }
  .benefits { position: absolute; left: 282px; top: 282px; width: 290px; list-style: none; }
  .benefit { display: flex; align-items: center; gap: 16px; height: 70px; margin-bottom: 6px; }
  .benefit-icon {
    flex: 0 0 60px; width: 60px; height: 60px; border-radius: 50%;
    background: var(--white); box-shadow: 0 2px 6px rgba(90, 85, 110, 0.15);
    display: flex; align-items: center; justify-content: center;
  }
  .benefit-text { font-size: 16px; line-height: 1.25; color: var(--ink-soft); }
  .volume { position: absolute; left: 262px; top: 512px; font-family: "Arimo", sans-serif; font-size: 18px; color: var(--violet); }
  .details {
    position: absolute; left: 40px; top: 552px; width: 508px; text-align: center;
    font-family: "Arimo", sans-serif; color: var(--violet);
  }
  .skin-types { font-size: 22px; line-height: 1.2; }
  .key-label { font-size: 12px; margin: 2px 0 5px; }
  .ingredient-name { font-size: 11px; line-height: 1.35; font-weight: 700; text-transform: uppercase; }
  .ingredient-desc { font-size: 11px; line-height: 1.35; margin-bottom: 2px; }
  .price {
    position: absolute; left: 300px; top: 692px;
    width: 132px; height: 48px; border-radius: 24px;
    background: var(--violet-dark); color: var(--white);
    font-family: "Arimo", sans-serif; font-weight: 700; font-size: 30px;
    display: flex; align-items: center; justify-content: center;
  }
</style>
</head>
<body>
  <article class="flyer">
    <h1 class="title"><span class="word-eye">EYE</span><span class="word-cream">CREAM</span></h1>
    <div class="title-rule"></div>

    <div class="product-photo" role="img" aria-label="Product photo: white Miroa skincare eye cream pump bottle, 15ml"></div>

    <ul class="benefits">
      <li class="benefit">
        <span class="benefit-icon">
          <svg width="34" height="34" viewBox="0 0 34 34" aria-hidden="true">
            <path d="M20 8 L23 17 L32 20 L23 23 L20 32 L17 23 L8 20 L17 17 Z" fill="#7a6fb0"/>
            <path d="M9 2 L10.5 6.5 L15 8 L10.5 9.5 L9 14 L7.5 9.5 L3 8 L7.5 6.5 Z" fill="#7a6fb0"/>
          </svg>
        </span>
        <span class="benefit-text">Visibly reduces<br>discoloration</span>
      </li>
      <li class="benefit">
        <span class="benefit-icon">
          <svg width="36" height="36" viewBox="0 0 36 36" aria-hidden="true">
            <path d="M18 16 C14 10 7 13 10 18 C12 21 18 25 18 25 C18 25 24 21 26 18 C29 13 22 10 18 16 Z" fill="#7a6fb0"/>
            <path d="M4 18 L4 26 L12 33 M32 18 L32 26 L24 33" stroke="#7a6fb0" stroke-width="3" fill="none" stroke-linecap="round"/>
          </svg>
        </span>
        <span class="benefit-text">Nourishes and<br>protect againts free<br>radicals</span>
      </li>
      <li class="benefit">
        <span class="benefit-icon">
          <svg width="32" height="32" viewBox="0 0 32 32" aria-hidden="true">
            <circle cx="16" cy="16" r="12" stroke="#7a6fb0" stroke-width="2" fill="none"/>
          </svg>
        </span>
        <span class="benefit-text">Smoothes out fine<br>lines and wrinkles</span>
      </li>
    </ul>

    <p class="volume">15ML</p>

    <section class="details">
      <p class="skin-types">All Skin types</p>
      <p class="key-label">Key ingredients</p>
      <p class="ingredient-name">Cucumis Sativus (Cucumber) Seed Oil</p>
      <p class="ingredient-desc">Highly moisturising with Vitamin E, it balances the skin &amp; encourages healthy skin regeneration.</p>
      <p class="ingredient-name">Kakadu Plum Extract</p>
      <p class="ingredient-desc">Rich in Vitamin C &amp; Gallic acid which has anti-inflammatory properties,<br>Can help reduce pigmentation and dark spots.</p>
    </section>

    <div class="price">$19</div>
  </article>
</body>
</html>
```